Tampa Bay fishing guide needs stunning website.

I currently have a site - www.reelcoveguide.net which I personally put together using the Pagely platform and I am looking for a redesign on a different platform (Sitecraft?) that will allow me to easily create landing pages in the future. Would like to have a block for visitors to opt in to newsletter. Need social media links on all pages.

I would like to let my visitors know that I am able to handle their fishing charter needs here in the Tampa Bay area, if I'm not available for the dates they are looking to go I can refer them to a reputable captain in the area.

Target Market(s)

United States

Industry/Entity Type

Tourism

Coding

Coded - Design and coding required

Number of Pages Required

5+ page

Font styles to use
Sans Serif

Colors
0355a3
3176b5
85abd2
fbf289

Requirements
Must have
• Mobile Responsive, Ability to insert Vantor Metrics, Chatterbox pixels, ability to add custom landing pages in future
Nice to have
• Clean, easy navigation

```html
<!DOCTYPE html>
<html lang="en">
<head>
<meta charset="utf-8">
<title>Harlow Charters – Tampa Bay Fishing Guide</title>
<link rel="stylesheet" href="https://fonts.googleapis.com/css2?family=Montserrat:wght@600;700;800&family=Open+Sans:wght@400;600;700&display=swap">
<style>
:root{
  --blue-deep:#0355a3;
  --blue-mid:#3176b5;
  --blue-light:#85abd2;
  --yellow:#fbf289;
  --ink:#333a40;
  --muted:#6b7680;
  --footer:#1e3a3a;
  --footer-dark:#142a2a;
  --white:#ffffff;
}
*{box-sizing:border-box;margin:0;padding:0}
html,body{width:1200px;height:2452px;overflow:hidden}
body{font-family:"Open Sans",Arial,sans-serif;color:var(--ink);background:var(--white);position:relative}

/* header */
.site-header{position:absolute;top:0;left:0;width:1200px;height:54px;background:var(--white);display:flex;align-items:center;justify-content:space-between;padding:0 150px;z-index:2;box-shadow:0 1px 4px rgba(0,0,0,.15)}
.brand{display:flex;align-items:center;gap:10px;font-family:"Montserrat",sans-serif;font-weight:700;font-size:22px;color:var(--blue-deep)}
.brand-dot{width:26px;height:26px;border-radius:50%;background:var(--blue-mid)}
.main-nav{display:flex;gap:4px}
.main-nav a{font-family:"Montserrat",sans-serif;font-weight:700;font-size:12px;color:var(--blue-deep);text-decoration:none;padding:8px 12px}
.main-nav a.active{background:var(--blue-deep);color:var(--white)}

/* hero */
.hero{position:absolute;top:0;left:0;width:1200px;height:596px;background:linear-gradient(160deg,#2f7a70 0%,#1f6a5c 40%,#3f8c7a 70%,#6aa3b0 100%)}
.hero-caption{position:absolute;left:150px;top:410px;width:440px;padding:18px 22px;background:rgba(0,0,0,.45);color:var(--yellow);font-family:"Open Sans",sans-serif;font-weight:600;font-size:25px;line-height:1.25}

/* intro */
.intro{position:absolute;top:612px;left:160px;width:880px;text-align:center}
.intro-kicker{font-size:11px;color:var(--muted);letter-spacing:.5px}
.intro-title{margin-top:10px;font-family:"Montserrat",sans-serif;font-weight:800;font-size:30px;line-height:1.25;letter-spacing:4px;color:var(--blue-deep)}
.intro-text{margin-top:16px;font-size:12px;line-height:1.6;color:var(--muted);text-align:left}
.intro-book{margin:6px 0;font-weight:700;color:var(--blue-deep);font-size:12px;text-align:center}

/* gallery */
.gallery{position:absolute;top:900px;left:160px;width:880px;display:grid;grid-template-columns:repeat(3,1fr);gap:8px}
.gallery-photo{height:234px}
.g1{background:linear-gradient(180deg,#8fb7cf,#5b8aa6)}
.g2{background:linear-gradient(180deg,#9aa9a2,#6d7d76)}
.g3{background:linear-gradient(180deg,#7ea3c0,#4c7493)}
.g4{background:linear-gradient(180deg,#c9cfc5,#7d8a80)}
.g5{background:linear-gradient(180deg,#a7bccb,#63819a)}
.g6{background:linear-gradient(180deg,#b7c8d6,#7c99b2)}

/* newsletter */
.newsletter{position:absolute;top:1400px;left:0;width:1200px;height:162px;background:var(--yellow);text-align:center;padding-top:30px}
.newsletter-title{font-family:"Montserrat",sans-serif;font-weight:800;font-size:30px;letter-spacing:5px;color:var(--blue-deep)}
.newsletter-form{margin-top:22px;display:flex;justify-content:center;gap:14px}
.newsletter-input{width:210px;height:32px;border:1px solid #ccc;background:var(--white);font-size:11px;color:#999;padding:0 10px;display:flex;align-items:center}
.newsletter-button{height:32px;padding:0 18px;background:var(--blue-deep);color:var(--white);font-size:12px;font-weight:600;display:flex;align-items:center}

/* call band */
.call-band{position:absolute;top:1562px;left:0;width:1200px;height:120px;background:var(--blue-deep);display:flex;align-items:center;justify-content:center;font-family:"Open Sans",sans-serif;font-weight:700;font-size:40px;color:var(--white)}

/* features */
.features{position:absolute;top:1700px;left:160px;width:880px;display:grid;grid-template-columns:1fr 1fr;gap:40px}
.feature-title{font-family:"Montserrat",sans-serif;font-weight:800;font-size:16px;color:var(--blue-deep);padding-bottom:8px;border-bottom:3px solid var(--blue-deep);display:inline-block}
.feature-photo{margin-top:14px;height:208px}
.f1{background:linear-gradient(180deg,#8fc0e0,#3176b5)}
.f2{background:linear-gradient(180deg,#c6d0c4,#8fa19a)}
.feature-text{margin-top:16px;font-size:15px;line-height:1.45;color:var(--muted);text-align:justify}
.feature-button{display:inline-block;margin-top:16px;background:var(--blue-deep);color:var(--white);font-size:12px;font-weight:600;padding:10px 22px}
.feature-center{text-align:center}

/* footer */
.site-footer{position:absolute;top:2180px;left:0;width:1200px;height:272px;background:linear-gradient(180deg,var(--footer),#183232)}
.footer-cols{position:absolute;top:22px;left:160px;width:880px;display:grid;grid-template-columns:1fr 1fr 1fr;gap:40px}
.footer-heading{font-family:"Montserrat",sans-serif;font-weight:700;font-size:14px;color:var(--blue-light);margin-bottom:10px}
.footer-heading.spaced{margin-top:18px}
.footer-list{list-style:none;font-size:11px;line-height:2.1;color:#d7e0e0}
.social-row{display:flex;gap:10px}
.social-dot{width:26px;height:26px;border-radius:50%;background:var(--blue-mid)}
.social-dot.alt{background:#c8473b}
.payment-row{display:flex;gap:6px}
.payment-card{width:38px;height:24px;background:#d7e0e0;border-radius:3px}
.footer-bottom{position:absolute;bottom:0;left:0;width:1200px;height:34px;background:var(--footer-dark);display:flex;align-items:center;justify-content:center;font-size:10px;color:#9fb0b0}
</style>
</head>
<body>

<section class="hero" role="img" aria-label="Photo of smiling anglers holding a fish on a boat over the blue-green waters of Tampa Bay"></section>

<header class="site-header">
  <div class="brand"><span class="brand-dot"></span>Harlow</div>
  <nav class="main-nav">
    <a class="active" href="#">HOME</a>
    <a href="#">ABOUT US</a>
    <a href="#">PICK UP LOCATIONS</a>
    <a href="#">RATES</a>
    <a href="#">CONTACT US</a>
    <a href="#">GIFT CARD</a>
  </nav>
</header>

<p class="hero-caption">Come fish with Tampa Bay, FL fishing guide, Tampa Bay fishing charter most respected Captain,25 year Native Guide</p>

<section class="intro">
  <p class="intro-kicker">TAMPA BAY FISHING CHARTERS FLORIDA | FISHING CHARTERS TAMPA BAY</p>
  <h1 class="intro-title">TAMPA BAY,FISHINGGUIDE,TAMPABAY<br>FISHINGCHARTERS</h1>
  <p class="intro-text">Capt. Wade Harlow, with over 25 years' experience, has been guiding anglers across Tampa Bay and nearby waters. Whether you are after snook, redfish, trout or tarpon, every trip is built around your group, your skill level and the season. Trips run year round from several convenient pickup points. Light tackle, live bait and a relaxed day on the water are all part of the plan. Call or book your date today.</p>
  <p class="intro-book">BOOK YOUR TRIP ONLINE HERE.</p>
  <p class="intro-text" style="margin-top:0">Fishing is available on half day and full day charters for families, friends, beginners and seasoned anglers alike. If the captain is booked on your dates, he will gladly refer you to a trusted local captain so you never miss a day on the water. Come see why so many guests return every season.</p>
</section>

<section class="gallery">
  <div class="gallery-photo g1" role="img" aria-label="Angler holding a large fish beside the boat"></div>
  <div class="gallery-photo g2" role="img" aria-label="Guest showing a catch on deck"></div>
  <div class="gallery-photo g3" role="img" aria-label="Fish being held up over the water"></div>
  <div class="gallery-photo g4" role="img" aria-label="Two anglers with rods on a charter"></div>
  <div class="gallery-photo g5" role="img" aria-label="Young angler with a trout"></div>
  <div class="gallery-photo g6" role="img" aria-label="Smiling guest in a cap holding a fish"></div>
</section>

<section class="newsletter">
  <h2 class="newsletter-title">NEWSLETTER SUBSCRIBE</h2>
  <div class="newsletter-form">
    <div class="newsletter-input">Enter name</div>
    <div class="newsletter-input">Enter email</div>
    <div class="newsletter-button">Subscribe Now</div>
  </div>
</section>

<section class="call-band">Call Capt. Wade (813) 555-0142</section>

<section class="features">
  <article class="feature">
    <h3 class="feature-title">FULL &amp; HALF DAY CHARTERS</h3>
    <div class="feature-photo f1" role="img" aria-label="Angler fighting a fish from the bow of a charter boat"></div>
    <p class="feature-text">Offering Tampa Bay, FL fishing charters on the beautiful waters of Tampa Bay, Fish with Capt. Wade Harlow, Tampa Bay, FL fishing guide for over 25 years.</p>
    <div class="feature-center"><span class="feature-button">Find Out More</span></div>
  </article>
  <article class="feature">
    <h3 class="feature-title">MULTIPLE PICKUP POINTS</h3>
    <div class="feature-photo f2" role="img" aria-label="Captain and guest holding a catch at the dock"></div>
    <p class="feature-text">Whether you're looking for a fishing charter/guide in Tampa, St. Pete, Clearwater or Bradenton, Capt. Wade can pick you up nearby. Click here for maps of pickup locations.</p>
    <div class="feature-center"><span class="feature-button">Maps &amp; Pickup Locations</span></div>
  </article>
</section>

<footer class="site-footer">
  <div class="footer-cols">
    <div>
      <h4 class="footer-heading">PICKUP LOCATIONS</h4>
      <ul class="footer-list">
        <li>Bayside Marina - St. Petersburg</li>
        <li>Sandpiper Landing - Gulf Shore</li>
        <li>Gulfview Boat Ramp</li>
        <li>Pelican Point Boat Ramp</li>
      </ul>
    </div>
    <div>
      <h4 class="footer-heading">CONTACT US</h4>
      <ul class="footer-list">
        <li>Ph : 813-555-0142</li>
        <li>E-Mail : info@reelcoveguide.net</li>
      </ul>
    </div>
    <div>
      <h4 class="footer-heading">PAYMENT OPTION</h4>
      <div class="payment-row">
        <span class="payment-card"></span><span class="payment-card"></span><span class="payment-card"></span><span class="payment-card"></span>
      </div>
      <h4 class="footer-heading spaced">FOLLOW US</h4>
      <div class="social-row">
        <span class="social-dot"></span><span class="social-dot"></span><span class="social-dot"></span><span class="social-dot alt"></span>
      </div>
    </div>
  </div>
  <div class="footer-bottom">Copyright © 2016. All Rights Reserved</div>
</footer>

</body>
</html>
```